New Business Card Design Project LORVANTI-Italy

we are LORVANTI-Italy
our company in the market for 3 years we are luxury cosmetic company and its about time for a facelift :)
i will like to have elegant luxurious and unique business card
that will give the person that get it a unique, luxurious and elegant impression
I'm VERY OPEN FOR NEW IDEAS , even duo i add a few files of things that i see on line and i like them

i add my logo as well
my website is LORVANTI.COM
(if you would like to see the main style that we have)

Target Market(s)

adult that have money :)

Industry/Entity Type

Business

Contact Information for Business Card

Name - Dario Lorvanti
Position - CEO and CO Founder
address - 4817 E Halvern
telephone - 555-384-1926
email - dario@lorvanti.com
fax - 555-384-1926
website - LORVANTI.COM

Colors
000000
959595
fbee3e
ffffff

Requirements
Must have
• big logo in GOLD color
• elegant look
• impressive
Nice to have
• not must but maybe classy pattern background
• not must but maybe emblem
• maybe clear plastic business card
Should not have
• colors
• images

```html
<!DOCTYPE html>
<html lang="en">
<head>
<meta charset="utf-8">
<title>LORVANTI Italy – Business Card</title>
<link href="https://fonts.googleapis.com/css2?family=Tinos:wght@400;700&family=PT+Sans:wght@400&display=swap" rel="stylesheet">
<style>
  :root {
    --backdrop-top: #c9c9c9;
    --backdrop-bottom: #ffffff;
    --card-black: #0c0c0c;
    --card-black-edge: #151515;
    --gold: #d8b24a;
    --white: #f2f2f2;
  }
  * { margin: 0; padding: 0; box-sizing: border-box; }
  html, body { width: 1200px; height: 900px; overflow: hidden; }
  body {
    position: relative;
    background: linear-gradient(to bottom, var(--backdrop-top) 0%, #e4e4e4 45%, var(--backdrop-bottom) 100%);
    font-family: "PT Sans", Arial, sans-serif;
  }
  .card {
    position: absolute;
    top: 184px;
    height: 490px;
    border-radius: 12px;
    background: linear-gradient(160deg, var(--card-black-edge), var(--card-black) 60%);
  }
  .card--front { left: 299px; width: 301px; }
  .card--back { left: 645px; width: 304px; }

  .front__mark {
    position: absolute;
    left: 50%; top: 38px;
    width: 104px; height: 104px;
    margin-left: -52px;
    border: 3px solid var(--gold);
    border-radius: 50%;
  }
  .front__brand {
    position: absolute;
    left: 0; right: 0; top: 164px;
    text-align: center;
    font-family: "Tinos", "Times New Roman", serif;
    font-weight: 400;
    font-size: 41px;
    letter-spacing: 1px;
    color: var(--gold);
  }
  .front__rule {
    position: absolute;
    left: 32px; right: 35px; top: 218px;
    height: 2px;
    background: var(--gold);
  }
  .front__region {
    position: absolute;
    left: 0; right: 0; top: 228px;
    text-align: center;
    font-family: "Tinos", "Times New Roman", serif;
    font-size: 18px;
    letter-spacing: 1px;
    color: var(--gold);
  }
  .person { position: absolute; left: 31px; top: 292px; }
  .person__name {
    font-family: "Tinos", "Times New Roman", serif;
    font-weight: 700;
    font-size: 18px;
    letter-spacing: 0.3px;
    color: var(--gold);
  }
  .person__role { font-size: 13px; color: var(--white); margin-top: 1px; }

  .contacts { position: absolute; left: 31px; top: 350px; list-style: none; }
  .contacts__item {
    display: flex; align-items: center;
    height: 20.5px;
    font-size: 13px;
    color: var(--white);
  }
  .contacts__icon { width: 14px; height: 14px; margin-right: 8px; flex: none; }
  .address {
    position: absolute; left: 28px; top: 443px;
    font-size: 13px; color: var(--white);
  }

  .back__emblem {
    position: absolute;
    left: 50px; top: 143px;
    width: 204px; height: 204px;
    border: 4px solid var(--gold);
    border-radius: 50%;
    display: flex; align-items: center; justify-content: center;
  }
  .back__brand {
    font-family: "Tinos", "Times New Roman", serif;
    font-weight: 400;
    font-size: 28px;
    letter-spacing: 1px;
    color: var(--gold);
  }
</style>
</head>
<body>
  <section class="card card--front" aria-label="Business card front">
    <div class="front__mark"></div>
    <div class="front__brand">LORVANTI</div>
    <div class="front__rule"></div>
    <div class="front__region">ITALY</div>

    <div class="person">
      <div class="person__name">DARIO LORVANTI</div>
      <div class="person__role">CEO and CO Founder</div>
    </div>

    <ul class="contacts">
      <li class="contacts__item">
        <svg class="contacts__icon" viewBox="0 0 14 14" aria-hidden="true">
          <circle cx="7" cy="7" r="7" fill="#d8b24a"/>
          <path d="M4 5.2h6v1.2H4z M5 6.4h4l1 3H4z" fill="#0c0c0c"/>
        </svg>555-384-1926
      </li>
      <li class="contacts__item">
        <svg class="contacts__icon" viewBox="0 0 14 14" aria-hidden="true">
          <circle cx="7" cy="7" r="7" fill="#d8b24a"/>
          <rect x="4.5" y="6" width="5" height="4" fill="#0c0c0c"/>
          <rect x="5.5" y="3.8" width="3" height="2.4" fill="none" stroke="#0c0c0c" stroke-width="0.9"/>
        </svg>555-384-1926
      </li>
      <li class="contacts__item">
        <svg class="contacts__icon" viewBox="0 0 14 14" aria-hidden="true">
          <circle cx="7" cy="7" r="7" fill="#d8b24a"/>
          <rect x="3.8" y="4.6" width="6.4" height="4.8" fill="#0c0c0c"/>
          <path d="M3.8 4.6 7 7.3 10.2 4.6" fill="none" stroke="#d8b24a" stroke-width="0.8"/>
        </svg>dario@lorvanti.com
      </li>
      <li class="contacts__item">
        <svg class="contacts__icon" viewBox="0 0 14 14" aria-hidden="true">
          <circle cx="7" cy="7" r="7" fill="#d8b24a"/>
          <circle cx="7" cy="7" r="3.2" fill="none" stroke="#0c0c0c" stroke-width="1"/>
          <path d="M3.8 7h6.4M7 3.8v6.4" stroke="#0c0c0c" stroke-width="0.7"/>
        </svg>LORVANTI.COM
      </li>
    </ul>

    <div class="address">4817 E Halvern</div>
  </section>

  <section class="card card--back" aria-label="Business card back">
    <div class="back__emblem">
      <span class="back__brand">LORVANTI</span>
    </div>
  </section>
</body>
</html>
```